Business Card

THIS IS THE CARD INFORMATION
DEVELOPMENT I FINANCING I PROPERTY MANAGEMENT
DANIEL OKAFOR
3182 SW 74th Terrace
Lakeview Pines, FL 33512
Telephone I 855.437.2618
Facsimile I 855.437.2675
Industry/Entity Type
Business

```html
<!DOCTYPE html>
<html lang="en">
<head>
<meta charset="utf-8">
<title>Ruiz Varela &amp; Company – Business Card</title>
<link href="https://fonts.googleapis.com/css2?family=Mulish:wght@400;600;800&display=swap" rel="stylesheet">
<style>
  :root {
    --stage: #2a0029;
    --ink: #2b2b2b;
    --brand: #a0208f;
    --brand-deep: #6a1e5e;
    --brand-glow: #b22a9f;
    --paper: #ffffff;
  }
  * { margin: 0; padding: 0; box-sizing: border-box; }
  html, body { width: 1200px; height: 1000px; overflow: hidden; }
  body {
    background: var(--stage);
    font-family: "Mulish", sans-serif;
    position: relative;
  }
  .card {
    position: absolute;
    width: 693px;
    height: 409px;
    overflow: hidden;
  }
  .card svg.card-art { position: absolute; inset: 0; }
  .card-front { left: 252px; top: 73px; background: var(--paper); color: var(--ink); }
  .card-back { left: 253px; top: 512px; color: var(--paper); }

  .front-tagline {
    position: absolute; left: 132px; top: 29px;
    font-size: 19px; font-weight: 400; letter-spacing: 0; white-space: nowrap;
  }
  .front-tagline .sep { font-weight: 400; margin: 0 2px; font-size: 25px; vertical-align: -3px; }
  .holder-name {
    position: absolute; left: 203px; top: 79px;
    font-size: 28px; font-weight: 400; color: var(--brand); letter-spacing: 0.5px;
  }
  .address {
    position: absolute; left: 203px; top: 132px;
    font-size: 17px; line-height: 26px;
  }
  .contact {
    position: absolute; left: 203px; top: 201px;
    font-size: 17px; line-height: 23.5px;
    display: grid; grid-template-columns: 93px auto;
  }
  .wordmark {
    position: absolute; font-weight: 800; line-height: 1; white-space: nowrap;
  }
  .wordmark .line-2 { display: block; text-align: right; }
  .front-wordmark { left: 296px; top: 312px; font-size: 48px; color: var(--ink); }
  .front-wordmark .line-2 { font-size: 25px; margin-top: 4px; color: var(--brand); }
  .back-wordmark { left: 187px; top: 124px; font-size: 62px; color: var(--paper); }
  .back-wordmark .line-2 { font-size: 31px; margin-top: 2px; }
  .back-tagline {
    position: absolute; left: 0; right: 0; top: 235px; text-align: center;
    font-size: 15px; font-weight: 600; letter-spacing: 0;
  }
  .back-tagline .dot { margin: 0 12px; }
  .website {
    position: absolute; left: 0; right: 0; top: 260px; text-align: center;
    font-size: 19px;
  }
</style>
</head>
<body>

<section class="card card-front" aria-label="Card front">
  <svg class="card-art" viewBox="0 0 693 409" width="693" height="409">
    <defs>
      <linearGradient id="towerFront" x1="0" y1="0" x2="1" y2="0">
        <stop offset="0" stop-color="#c97fbd" stop-opacity="0.5"/>
        <stop offset="1" stop-color="#a0469a" stop-opacity="0.7"/>
      </linearGradient>
    </defs>
    <polygon points="0,0 80,0 370,409 0,409" fill="#f4e6f1"/>
    <polygon points="0,195 210,409 0,409" fill="#dcb6d6"/>
    <polygon points="440,150 693,110 693,409 430,409" fill="#f6f4f6"/>
    <circle cx="239" cy="344" r="42" fill="var(--brand)"/>
    <rect x="36" y="257" width="120" height="152" fill="url(#towerFront)" role="img" aria-label="Stylised city towers illustration"/>
  </svg>
  <p class="front-tagline">DEVELOPMENT<span class="sep">/</span>FINANCING<span class="sep">/</span>PROPERTY MANAGEMENT</p>
  <h1 class="holder-name">DANIEL OKAFOR</h1>
  <p class="address">3182 SW 74th Terrace<br>Lakeview Pines, FL 33512</p>
  <div class="contact">
    <span>Telephone</span><span>: 855.437.2618</span>
    <span>Facsimile</span><span>: 855.437.2675</span>
    <span>Email</span><span>: dokafor@ruizvarelaandco.com</span>
  </div>
  <p class="wordmark front-wordmark">RUIZ VARELA<span class="line-2">&amp; COMPANY</span></p>
</section>

<section class="card card-back" aria-label="Card back">
  <svg class="card-art" viewBox="0 0 693 409" width="693" height="409">
    <defs>
      <radialGradient id="backGlow" cx="0.5" cy="0.42" r="0.65">
        <stop offset="0" stop-color="var(--brand-glow)"/>
        <stop offset="1" stop-color="var(--brand-deep)"/>
      </radialGradient>
      <linearGradient id="towerBack" x1="0" y1="0" x2="1" y2="0">
        <stop offset="0" stop-color="#b23aa2"/>
        <stop offset="1" stop-color="#7d2472"/>
      </linearGradient>
    </defs>
    <rect width="693" height="409" fill="url(#backGlow)"/>
    <polygon points="0,0 60,0 300,300 0,180" fill="#5a1a52" opacity="0.35"/>
    <polygon points="0,200 210,409 0,409" fill="#8a2a7e" opacity="0.5"/>
    <circle cx="113" cy="163" r="51" fill="var(--paper)"/>
    <rect x="37" y="258" width="120" height="151" fill="url(#towerBack)" opacity="0.8" role="img" aria-label="Stylised city towers illustration"/>
  </svg>
  <p class="wordmark back-wordmark">RUIZ VARELA<span class="line-2">&amp; COMPANY</span></p>
  <p class="back-tagline">DEVELOPMENT<span class="dot">•</span>FINANCING<span class="dot">•</span>PROPERTY MANAGEMENT</p>
  <p class="website">www.ruizvarelaandco.com</p>
</section>

</body>
</html>
```